Web design for business website

I need a web design for a business website for one of our clients who is specialized in alarm management software. I would like you to design 3 web pages, one for each of the 3 pages. You need to process the corporate identity of our client to the web design. This means the colors of the logo (red and black) should definitely show up on all of the 3 pages. Find the logo file for the logo of our customer. To increase readability I suggest you use a white/light background. All suggestions are welcome.

Please kindly download atttached Webdesign.zip and read the project brief first. The project brief refers to all other files of the zip file. Your design must have exactly the same structure as the wireframes.
Updates

Target Market(s)

B2B, Alarm management

Industry/Entity Type

Business

Number of Pages Required

3 page

Requirements
Must have
• The web design must have exactly the same structure as the wireframes and needs to contain the colors of the company logo.

```html
<!DOCTYPE html>
<html lang="en">
<head>
<meta charset="utf-8">
<title>Valerion – Real-time reasoning solutions</title>
<link href="https://fonts.googleapis.com/css2?family=Open+Sans:wght@400;600;700&family=Oswald:wght@400;500;700&display=swap" rel="stylesheet">
<style>
:root{
  --red:#e2231a;
  --red-dark:#b5140e;
  --ink:#1d1d1d;
  --text:#555;
  --muted:#888;
  --line:#e3e3e3;
  --white:#fff;
  --footer:#1b1b1b;
  --footer-text:#9a9a9a;
}
*{margin:0;padding:0;box-sizing:border-box}
html,body{width:753px;height:1200px;overflow:hidden;background:var(--white)}
body{font-family:"Open Sans",Arial,sans-serif;color:var(--text);font-size:8px}
.page{position:relative;width:753px;height:1200px;overflow:hidden}

.topbar{height:14px;background:#2a2a2a;color:#bbb;font-size:6px;display:flex;justify-content:space-between;align-items:center;padding:0 22px}
.topbar .right span{margin-left:10px}

.header{height:132px;display:flex;justify-content:space-between;align-items:flex-start;padding:24px 22px 0}
.brand-name{font-family:"Oswald",Arial,sans-serif;font-weight:700;font-size:30px;color:var(--ink);letter-spacing:1px;line-height:1;display:block}
.brand-tag{font-size:6px;color:var(--muted);display:block;margin-top:3px}
.header-actions{display:flex;gap:4px;margin-top:10px}
.header-actions span{background:var(--red);color:#fff;font-size:6px;font-weight:600;padding:6px 10px}
.header-actions span.dark{background:#333}

.nav{height:12px;background:var(--red);display:flex;padding-left:22px}
.nav a{color:#fff;font-size:6px;font-weight:700;text-decoration:none;padding:0 14px;line-height:12px;text-transform:uppercase}
.nav a.active{background:var(--red-dark)}

.hero{position:absolute;top:158px;left:0;width:753px;height:206px;background:linear-gradient(180deg,#7f93a8 0%,#c9a27a 45%,#e9a54f 62%,#5a5346 78%,#3a4a34 100%)}
.hero-arrow{position:absolute;top:92px;width:14px;height:22px;background:rgba(0,0,0,.45)}
.hero-arrow svg{display:block;margin:6px auto}
.hero-arrow.prev{left:14px}.hero-arrow.next{right:14px;background:var(--red)}
.hero-card{position:absolute;left:176px;top:74px;width:284px;padding:10px 14px 10px;background:rgba(255,255,255,.92)}
.hero-card .hello{font-family:"Oswald",Arial,sans-serif;font-size:10px;color:var(--ink);letter-spacing:1px;line-height:1.2}
.hero-card .big{font-family:"Oswald",Arial,sans-serif;font-size:26px;font-weight:700;color:var(--red);line-height:1}
.hero-card .slogan{position:absolute;left:128px;top:30px;font-size:7.5px;color:var(--ink)}
.hero-card p{font-size:5px;color:var(--text);margin-top:3px;width:230px;line-height:1.5}
.btn{display:inline-block;background:var(--red);color:#fff;font-size:6px;font-weight:700;padding:7px 14px;text-transform:uppercase}
.hero-card .btn{margin-top:5px;padding:5px 12px}

.about{position:absolute;top:372px;left:0;width:753px;height:271px}
.about-text{position:absolute;left:22px;top:44px;width:340px}
.section-title{font-family:"Oswald",Arial,sans-serif;font-size:22px;font-weight:500;color:var(--red);letter-spacing:1px;line-height:1.2}
.about-text p{font-size:6px;line-height:1.6;margin-top:6px}
.about-text .btn{margin-top:22px}
.about-photo{position:absolute;left:384px;top:0;width:344px;height:271px;background:linear-gradient(160deg,#c9d3dc 0%,#8a9cae 50%,#44536a 100%)}

.clients{position:absolute;top:680px;left:0;width:753px;text-align:center}
.clients h2{font-family:"Oswald",Arial,sans-serif;font-size:17px;font-weight:500;color:var(--red);letter-spacing:1px;line-height:1.2}
.clients .rule{width:200px;height:1px;background:var(--line);margin:5px auto}
.clients .sub{font-size:6.5px;color:var(--muted)}
.client-row{display:flex;justify-content:space-between;align-items:center;padding:0 40px;margin-top:52px}
.client{font-size:10px;font-weight:700;color:#6d6d6d}

.footer{position:absolute;top:921px;left:0;width:753px;height:279px;background:var(--footer);color:var(--footer-text)}
.footer h3{font-family:"Oswald",Arial,sans-serif;font-size:20px;font-weight:500;color:var(--red);letter-spacing:1px;line-height:1.2}
.follow{position:absolute;left:22px;top:30px}
.socials{display:flex;gap:4px;margin-top:12px}
.socials span{width:18px;height:18px;background:#3a3a3a;display:block}
.socials span:first-child{background:var(--red)}
.subscribe{position:absolute;left:240px;top:30px}
.subscribe form{display:flex;margin-top:12px}
.subscribe .field{width:300px;height:18px;background:#fff;color:var(--muted);font-size:6px;padding:5px 8px}
.subscribe .btn{padding:6px 12px;height:18px}
.footer-cols{position:absolute;left:22px;top:104px;width:710px;display:flex;justify-content:space-between;border-top:1px solid #2e2e2e;padding-top:12px}
.footer-cols div{width:120px}
.footer-cols h4{font-size:6.5px;color:#ccc;text-transform:uppercase;margin-bottom:6px}
.footer-cols li{list-style:none;font-size:6px;line-height:1.7}
.footer-cols li.hot{color:var(--red)}
.copyright{position:absolute;bottom:10px;width:100%;text-align:center;font-size:5.5px;color:#777}
</style>
</head>
<body>
<div class="page">
  <div class="topbar">
    <span>☎ +10 (0)55 0100 200</span>
    <span class="right"><span>Preferred language</span><span>EN</span></span>
  </div>

  <header class="header">
    <div class="brand">
      <span class="brand-name">VALERION</span>
      <span class="brand-tag">Real-time reasoning solutions</span>
    </div>
    <div class="header-actions"><span>SITEMAP</span><span class="dark">LOG IN</span><span class="dark">SEARCH</span><span>EN</span></div>
  </header>

  <nav class="nav">
    <a class="active">Home</a><a>Industry</a><a>Telecom</a><a>Power</a><a>Utilities</a><a>Infra</a><a>Store</a>
  </nav>

  <section class="hero" role="img" aria-label="Refinery at sunset behind a green field">
    <span class="hero-arrow prev"><svg width="6" height="10" viewBox="0 0 6 10"><path d="M5 1L1 5l4 4" stroke="#fff" fill="none" stroke-width="1.5"/></svg></span>
    <span class="hero-arrow next"><svg width="6" height="10" viewBox="0 0 6 10"><path d="M1 1l4 4-4 4" stroke="#fff" fill="none" stroke-width="1.5"/></svg></span>
    <div class="hero-card">
      <div class="hello">HELLO WE ARE</div>
      <div class="big">VALERION</div>
      <div class="slogan">Real-time reasoning solutions</div>
      <p>We turn raw alarm data into clear decisions, helping operators act faster and keep critical plants running safely every day.</p>
      <span class="btn">Read more</span>
    </div>
  </section>

  <section class="about">
    <div class="about-text">
      <h2 class="section-title">ABOUT US</h2>
      <p>Companies have invested to get data out of processes. New technologies have been developed to get more data out of the machines and plants, yet the crucial link between data and action is often missing. Operators still face floods of alarms with little context and must rely on experience to decide what matters most.</p>
      <p>Our technology applies real-time reasoning to events in the field, filtering noise, grouping related alarms and pointing to root causes, so that teams can respond with confidence before small issues grow into costly outages.</p>
      <span class="btn">Learn more</span>
    </div>
    <div class="about-photo" role="img" aria-label="Two engineers in hard hats at an industrial plant"></div>
  </section>

  <section class="clients">
    <h2>CLIENTS THAT TRUST US</h2>
    <div class="rule"></div>
    <p class="sub">Some of our clients that trust us, be shore to be one of them.</p>
    <div class="client-row">
      <span class="client">Dunecor</span>
      <span class="client">Corvane</span>
      <span class="client">Ostrel</span>
      <span class="client">Kelvor</span>
      <span class="client">Brouwmar</span>
      <span class="client">Pectra</span>
      <span class="client">NORDHAV OIL</span>
    </div>
  </section>

  <footer class="footer">
    <div class="follow">
      <h3>FOLLOW US ON :</h3>
      <div class="socials"><span></span><span></span><span></span><span></span><span></span></div>
    </div>
    <div class="subscribe">
      <h3>SUBSCRIBE NOW :</h3>
      <form><div class="field">Enter Your Email Adress</div><span class="btn">Subscribe</span></form>
    </div>
    <div class="footer-cols">
      <div><h4>Solutions</h4><ul><li class="hot">Alarm Reasoning</li><li>Event Analysis</li><li>Root Cause</li><li>Reporting</li></ul></div>
      <div><h4>Industries</h4><ul><li>Industry</li><li>Telecom</li><li>Power</li><li>Utilities</li><li>Infra</li></ul></div>
      <div><h4>About us</h4><ul><li>Company</li><li>Careers</li><li>Partners</li><li>Contact</li></ul></div>
      <div><h4>News</h4><ul><li>Latest News</li><li>Events</li><li>Webinars</li><li>Press</li><li>Archive</li></ul></div>
      <div><h4>Contact us</h4><ul><li>+10 (0)55 0100 200</li><li>info@valerion.example</li><li>12 Example Street, Testville</li></ul></div>
    </div>
    <div class="copyright">Copyright © 2015 VALERION. All rights reserved.</div>
  </footer>
</div>
</body>
</html>
```